FinTech company looking to revamp and expand client-facing interface for our financial models

Pellworth Engines currently has a very simple website that allows clients to interact with our financial models. We are looking to completely redesign the current site and add several extra pages to provide extra functionality. We want the design to have a modern, slick feel, that will work on both a desktop or a tablet. It should be straightforward for clients to move between different pages at any time, and clear from the layout how to interact with the more advanced features. We have included screenshots of existing pages in the attached design brief, as well as sketches of the functionality required by the new pages, but can't provide a direct link to the current site.
Target Market(s)
Professional investors that will be paying to access the interface
Industry/Entity Type
Finance
Number of Pages Required
4 page
Colors
Designer to choose colors to be used in the design.
Look and feel
Each slider illustrates characteristics of the customer's brand and the style your logo design should communicate.

```html
<!DOCTYPE html>
<html lang="en">
<head>
<meta charset="utf-8">
<title>Pellworth Engines – Portfolio</title>
<link href="https://fonts.googleapis.com/css2?family=Open+Sans:wght@400;600;700&family=Tinos&display=swap" rel="stylesheet">
<style>
:root{
  --teal:#016767;
  --navy:#0b2e5e;
  --ink:#1a1a1a;
  --green:#1fb11f;
  --bar-green:#00cc00;
  --red:#b5121b;
  --bar-red:#f20000;
  --row-alt:#f0f0f0;
  --line:#dedede;
  --blue-dot:#3d6eaf;
  --olive-dot:#b6b53a;
  --bg-top:#e4e4e4;
  --bg-bottom:#f8f8f8;
}
*{box-sizing:border-box;margin:0;padding:0}
html,body{width:1200px;height:1149px;overflow:hidden}
body{font-family:"Open Sans",sans-serif;color:var(--ink);background:linear-gradient(var(--bg-top) 55px,var(--bg-bottom) 400px,#f9f9f9)}
.canvas{position:relative;width:1200px;height:1149px}

.topbar{position:absolute;left:0;top:0;width:1200px;height:55px;background:#fff;box-shadow:0 2px 8px rgba(0,0,0,.08)}
.brand{position:absolute;left:67px;top:0;line-height:55px;font-weight:700;font-size:17px;letter-spacing:.2px}
.range-tab{position:absolute;top:0;height:55px;line-height:55px;text-align:center;font-weight:700;font-size:14px;border-left:1px solid var(--line)}
.nav-tab{position:absolute;top:0;height:55px;display:flex;align-items:center;justify-content:center;gap:8px;font-weight:700;font-size:13px;border-left:1px solid var(--line)}
.nav-tab svg{width:22px;height:22px}
.nav-tab.is-active{background:var(--navy);color:#fff;border-left-color:var(--navy)}

.members{position:absolute;left:65px;top:92px;width:517px;height:480px;background:#fff;box-shadow:0 2px 8px rgba(0,0,0,.12);overflow:hidden}
.members-title{height:46px;background:#1b1b1b;color:#fff;text-align:center;line-height:46px;font-weight:600;font-size:16px;border-radius:3px 3px 0 0}
.members-head{display:flex;height:47px;background:var(--teal);color:#fff;font-weight:600;font-size:15.5px}
.members-head div{line-height:47px;text-align:center}
.col-name{width:240px;border-right:1px solid rgba(255,255,255,.25)}
.col-size{width:240px}
.member-row{display:flex;height:64.5px;align-items:center;font-size:16px;width:480px}
.member-row:nth-child(even){background:var(--row-alt)}
.member-row .col-name{display:flex;align-items:center;height:100%;padding-left:46px;gap:14px;border-right:1px solid #e6e6e6}
.member-row .col-size{text-align:center}
.member-row svg{width:24px;height:24px}
.member-list{position:absolute;left:0;top:93px}
.scroll-track{position:absolute;left:480px;top:93px;width:37px;height:387px;background:#d4d4d4}
.scroll-rail{position:absolute;left:10px;top:25px;width:18px;height:345px;background:#fff;border-radius:9px}
.scroll-thumb{position:absolute;left:10px;top:25px;width:18px;height:70px;background:#8d8d8d;border-radius:9px}

.actions{position:absolute;left:65px;top:591px;display:flex;gap:9px}
.btn{height:37px;display:flex;align-items:center;gap:8px;padding:0 15px;color:#fff;font-weight:700;font-size:14.5px;border-radius:3px}
.btn svg{width:20px;height:20px}
.btn-add{background:var(--navy);width:164px}
.btn-save{background:var(--green);width:177px}
.btn-clear{background:var(--red);width:131px}

.sensitivities{position:absolute;left:618px;top:92px;width:517px;height:323px;background:#fff;box-shadow:0 2px 8px rgba(0,0,0,.12);border-radius:3px 3px 0 0;overflow:hidden}
.sens-title{height:65px;background:var(--teal);color:#fff;text-align:center;line-height:65px;font-weight:600;font-size:16px}
.sens-row{position:relative;height:64.5px;display:flex;align-items:center}
.sens-row:nth-child(odd){background:var(--row-alt)}
.sens-label{position:absolute;left:26px;font-size:16px}
.gauge{position:absolute;left:198px;top:8px;width:297px;height:48px;background:#e9e9e9}
.gauge-box{position:absolute;left:10px;top:6px;width:277px;height:35px;background:#fff;border:1px solid #d6d6d6}
.gauge-quarter{position:absolute;top:0;width:1px;height:100%;background:#ececec}
.gauge-zero{position:absolute;left:139px;top:-7px;width:1px;height:48px;background:#777}
.gauge-bar{position:absolute;top:0;height:100%}
.gauge-bar.pos{left:139px;background:var(--bar-green)}
.gauge-bar.neg{background:var(--bar-red)}
.gauge-value{position:absolute;top:0;line-height:33px;font-size:15px;font-family:"Open Sans",sans-serif;letter-spacing:-.5px}

.chart-card{position:absolute;left:65px;top:683px;width:1070px;height:392px;background:#fff;box-shadow:0 2px 8px rgba(0,0,0,.1)}
.chart-tabs{position:absolute;left:0;top:0;width:1070px;height:79px;background:#efefef}
.chart-tab{position:absolute;top:46px;height:33px;line-height:33px;text-align:center;background:#fff;font-weight:600;font-size:16px;width:83px}
.chart-tab.is-current{background:var(--teal);color:#fff;width:143px}
.chart-tab.is-hover{background:#d0d0d0;top:37px;height:42px;line-height:36px;color:#444}
.plot{position:absolute;left:0;top:79px}
.plot text{font-family:"Open Sans",sans-serif;font-size:11.5px;fill:#555}
.plot .legend-title{font-family:"Tinos",serif;font-size:11.5px;fill:#333}
</style>
</head>
<body>
<div class="canvas">

  <header class="topbar">
    <div class="brand">PELLWORTH</div>
    <div class="range-tab" style="left:180px;width:84px">250D</div>
    <div class="range-tab" style="left:264px;width:83px">83D</div>
    <div class="range-tab" style="left:347px;width:83px">42D</div>
    <div class="range-tab" style="left:430px;width:1px"></div>

    <div class="nav-tab" style="left:555px;width:130px">
      <svg viewBox="0 0 24 24" fill="none" stroke="#1a1a1a" stroke-width="2.2" stroke-linejoin="round"><path d="M3 12 12 4l9 8"/><path d="M6 10v10h4v-6h4v6h4V10"/></svg>MODELS
    </div>
    <div class="nav-tab" style="left:685px;width:163px">
      <svg viewBox="0 0 24 24" fill="#1a1a1a"><circle cx="12" cy="12" r="2.5"/><circle cx="12" cy="3" r="1.5"/><circle cx="12" cy="21" r="1.5"/><circle cx="3" cy="12" r="1.5"/><circle cx="21" cy="12" r="1.5"/><circle cx="5.6" cy="5.6" r="1.5"/><circle cx="18.4" cy="18.4" r="1.5"/><circle cx="18.4" cy="5.6" r="1.5"/><circle cx="5.6" cy="18.4" r="1.5"/><circle cx="12" cy="7.5" r="1.2"/><circle cx="12" cy="16.5" r="1.2"/><circle cx="7.5" cy="12" r="1.2"/><circle cx="16.5" cy="12" r="1.2"/></svg>SENSITIVITIES
    </div>
    <div class="nav-tab is-active" style="left:848px;width:149px">
      <svg viewBox="0 0 24 24" fill="none" stroke="#fff" stroke-width="1.8"><circle cx="7" cy="7" r="4"/><circle cx="17" cy="7" r="4"/><circle cx="7" cy="17" r="4"/><circle cx="17" cy="17" r="4"/></svg>PORTFOLIO
    </div>
    <div class="nav-tab" style="left:997px;width:139px;border-right:1px solid var(--line)">
      <svg viewBox="0 0 24 24" fill="none" stroke="#1a1a1a" stroke-width="2"><rect x="2" y="3" width="20" height="18"/><path d="M5 16l4-6 3 4 3-6 4 8"/></svg>BACKTEST
    </div>
  </header>

  <section class="members">
    <div class="members-title">Current Members</div>
    <div class="members-head"><div class="col-name">Members Name</div><div class="col-size">Size</div></div>
    <div class="member-list">
      <div class="member-row"><div class="col-name"><svg viewBox="0 0 24 24" fill="none" stroke="#b01e24" stroke-width="2"><circle cx="12" cy="12" r="10.5"/><path d="M7 12h10"/></svg>Member 1</div><div class="col-size">0.2</div></div>
      <div class="member-row"><div class="col-name"><svg viewBox="0 0 24 24" fill="none" stroke="#b01e24" stroke-width="2"><circle cx="12" cy="12" r="10.5"/><path d="M7 12h10"/></svg>Member 2</div><div class="col-size">0.5</div></div>
      <div class="member-row"><div class="col-name"><svg viewBox="0 0 24 24" fill="none" stroke="#b01e24" stroke-width="2"><circle cx="12" cy="12" r="10.5"/><path d="M7 12h10"/></svg>Member 3</div><div class="col-size">-0.3</div></div>
      <div class="member-row"><div class="col-name"><svg viewBox="0 0 24 24" fill="none" stroke="#b01e24" stroke-width="2"><circle cx="12" cy="12" r="10.5"/><path d="M7 12h10"/></svg>Member 4</div><div class="col-size">0.2</div></div>
      <div class="member-row"><div class="col-name"><svg viewBox="0 0 24 24" fill="none" stroke="#b01e24" stroke-width="2"><circle cx="12" cy="12" r="10.5"/><path d="M7 12h10"/></svg>Member 5</div><div class="col-size">0.5</div></div>
      <div class="member-row"><div class="col-name"><svg viewBox="0 0 24 24" fill="none" stroke="#b01e24" stroke-width="2"><circle cx="12" cy="12" r="10.5"/><path d="M7 12h10"/></svg>Member 6</div><div class="col-size">-0.3</div></div>
    </div>
    <div class="scroll-track"><div class="scroll-rail"></div><div class="scroll-thumb"></div></div>
  </section>

  <div class="actions">
    <div class="btn btn-add"><svg viewBox="0 0 24 24" fill="none" stroke="#fff" stroke-width="1.8"><circle cx="12" cy="12" r="10"/><path d="M12 7v10M7 12h10"/></svg>ADD MEMBERS</div>
    <div class="btn btn-save"><svg viewBox="0 0 24 24" fill="none" stroke="#fff" stroke-width="3.5" stroke-linecap="round" stroke-linejoin="round"><path d="M3 13l6 6L21 5"/></svg>SAVE PORTFOLIO</div>
    <div class="btn btn-clear"><svg viewBox="0 0 24 24" fill="none" stroke="#fff" stroke-width="3.5" stroke-linecap="round"><path d="M4 4l16 16M20 4 4 20"/></svg>CLEAR ALL</div>
  </div>

  <section class="sensitivities">
    <div class="sens-title">Sensitivities</div>
    <div>
      <div class="sens-row" style="background:var(--row-alt)">
        <span class="sens-label">A-Lorem ipsum dolor</span>
        <div class="gauge"><div class="gauge-box">
          <div class="gauge-quarter" style="left:69px"></div><div class="gauge-quarter" style="left:208px"></div>
          <div class="gauge-bar pos" style="width:62px"></div>
          <span class="gauge-value" style="left:210px">0.9</span>
          <div class="gauge-zero"></div>
        </div></div>
      </div>
      <div class="sens-row" style="background:#fff">
        <span class="sens-label">B-Lorem ipsum dolor</span>
        <div class="gauge"><div class="gauge-box">
          <div class="gauge-quarter" style="left:69px"></div><div class="gauge-quarter" style="left:208px"></div>
          <div class="gauge-bar pos" style="width:50px"></div>
          <span class="gauge-value" style="left:198px">0.7</span>
          <div class="gauge-zero"></div>
        </div></div>
      </div>
      <div class="sens-row" style="background:var(--row-alt)">
        <span class="sens-label">C-Lorem ipsum dolor</span>
        <div class="gauge"><div class="gauge-box">
          <div class="gauge-quarter" style="left:69px"></div><div class="gauge-quarter" style="left:208px"></div>
          <div class="gauge-bar neg" style="left:102px;width:37px"></div>
          <span class="gauge-value" style="left:66px">-0.6</span>
          <div class="gauge-zero"></div>
        </div></div>
      </div>
      <div class="sens-row" style="background:#fff">
        <span class="sens-label">D-Lorem ipsum dolor</span>
        <div class="gauge"><div class="gauge-box">
          <div class="gauge-quarter" style="left:69px"></div><div class="gauge-quarter" style="left:208px"></div>
          <div class="gauge-bar neg" style="left:122px;width:17px"></div>
          <span class="gauge-value" style="left:86px">-0.3</span>
          <div class="gauge-zero"></div>
        </div></div>
      </div>
    </div>
  </section>

  <section class="chart-card">
    <div class="chart-tabs">
      <div class="chart-tab is-current" style="left:50px">Chart</div>
      <div class="chart-tab" style="left:198px">#1</div>
      <div class="chart-tab" style="left:286px">#2</div>
      <div class="chart-tab" style="left:373px">#3</div>
      <div class="chart-tab is-hover" style="left:461px">#4</div>
    </div>
    <svg class="plot" width="1070" height="313" viewBox="70 825 1160 340">
      <g stroke="#eeeeee" stroke-width="1">
        <path d="M182 870V1075M324 870V1075M465 870V1075M605 870V1075M742 870V1075M882 870V1075M1022 870V1075"/>
        <path d="M182 888H1076M182 925H1076M182 962H1076M182 1000H1076M182 1037H1076"/>
      </g>
      <path d="M182 1075H1076" stroke="#666" stroke-width="1.2"/>
      <g text-anchor="end">
        <text x="151" y="892">100</text><text x="151" y="929">80</text><text x="151" y="966">60</text>
        <text x="151" y="1004">40</text><text x="151" y="1041">20</text><text x="151" y="1079">0</text>
      </g>
      <g text-anchor="middle">
        <text x="182" y="1100">Jul 2018</text><text x="324" y="1100">Sep 2018</text><text x="465" y="1100">Nov 2018</text>
        <text x="605" y="1100">Jan 2019</text><text x="742" y="1100">Mar 2019</text><text x="882" y="1100">May 2019</text>
        <text x="1022" y="1100">Jul 2019</text>
      </g>

      <g stroke-linecap="round" fill="none">
        <path d="M202 888H282" stroke="var(--olive-dot)" stroke-width="7" stroke-dasharray="0 6"/>
        <path d="M740 892H1010" stroke="var(--olive-dot)" stroke-width="7" stroke-dasharray="0 6"/>
        <path stroke="var(--olive-dot)" stroke-width="7" d="M285 890h0M290 900h0M295 905h0M300 895h0M310 890h0M318 895h0M325 897h0M333 900h0M336 955h0M340 985h0M345 1000h0M350 965h0M352 985h0M355 1000h0M362 1005h0M365 985h0M370 995h0M372 980h0M378 990h0M382 950h0M385 945h0M390 925h0M395 915h0M400 888h0M405 893h0M410 890h0M415 950h0M418 960h0M420 968h0M425 978h0M430 970h0M432 1020h0M436 1050h0M440 1040h0M445 1030h0M450 1050h0M458 1030h0M462 1018h0M470 1065h0M475 1068h0M480 1062h0M485 1055h0M490 1050h0M495 1045h0M500 1040h0M510 1010h0M518 1030h0M525 1015h0M528 990h0M532 970h0M538 965h0M540 888h0M548 895h0M555 890h0M562 887h0M570 890h0M578 1063h0M590 1058h0M598 1065h0M605 1050h0M610 1055h0M618 1045h0M625 1055h0M632 1060h0M640 1050h0M645 1035h0M650 1025h0M655 1020h0M658 1000h0M660 988h0M655 953h0M668 952h0M672 910h0M675 915h0M686 908h0M690 965h0M695 1030h0M700 1035h0M702 1045h0M705 915h0M708 925h0M712 945h0M718 940h0M720 988h0M722 900h0M730 905h0M735 915h0M740 902h0M745 895h0M752 905h0M755 900h0"/>
        <path d="M590 888H1025" stroke="var(--blue-dot)" stroke-width="7" stroke-dasharray="0 6"/>
        <path stroke="var(--blue-dot)" stroke-width="7" d="M205 900h0M210 892h0M216 898h0M220 893h0M203 953h0M223 968h0M255 965h0M268 968h0M225 1000h0M232 997h0M236 1015h0M240 1020h0M238 1030h0M250 1022h0M258 990h0M262 993h0M270 990h0M276 1028h0M285 1020h0M290 1002h0M296 1000h0M300 1025h0M305 1018h0M312 1022h0M318 1030h0M320 1020h0M332 1035h0M338 1050h0M345 1055h0M352 1048h0M360 1055h0M368 1045h0M375 1050h0M382 1030h0M388 1025h0M395 1018h0M400 1030h0M405 1022h0M412 1040h0M418 1030h0M425 1045h0M432 1030h0M434 1070h0M448 1045h0M455 1055h0M462 1058h0M465 944h0M468 918h0M475 915h0M480 900h0M485 910h0M490 925h0M495 1025h0M500 1040h0M505 1030h0M510 1015h0M520 1010h0M525 1040h0M532 993h0M540 995h0M542 908h0M548 900h0M555 892h0M562 897h0M570 905h0M575 898h0"/>
        <path stroke="#4aa03c" stroke-width="7" d="M1000 1072h0M1005 1072h0M1010 1072h0"/>
      </g>

      <text class="legend-title" x="1132" y="890">Names</text>
      <g>
        <circle cx="1114" cy="886" r="3.5" fill="#8fb6d8"/><circle cx="1114" cy="905" r="3.5" fill="#f3ad6b"/>
        <circle cx="1114" cy="923" r="3.5" fill="#3f9a3f"/><circle cx="1114" cy="942" r="3.5" fill="#e07a7a"/>
        <circle cx="1114" cy="961" r="3.5" fill="#b79ad3"/><circle cx="1114" cy="980" r="3.5" fill="#a98f85"/>
        <circle cx="1114" cy="998" r="3.5" fill="#eab3d6"/><circle cx="1114" cy="1017" r="3.5" fill="#c2c2c2"/>
        <circle cx="1114" cy="1035" r="3.5" fill="var(--olive-dot)"/><circle cx="1114" cy="1054" r="3.5" fill="#8ed9e3"/>
        <circle cx="1114" cy="1073" r="3.5" fill="var(--blue-dot)"/>
      </g>
    </svg>
  </section>

</div>
</body>
</html>
```